Tech business card design

We need an amazing business card design for our new business 'Pexla' a marketing tech startup based in Sydney, Australia. We provide an online marketplace for businesses to search and buy advertising media, connect with service providers and learn more about marketing. We wish to communicate 'cool tech', reliability and professionalism and design based around our logo.

Target Market(s)

Business Owners

Contact Information for Business Card

Name
Position
Email Address
Website
Phone Number

Font styles to use
Other font styles liked:
• Avenir & Avenir Next

Colors

Designer to choose colors to be used in the design.

```html
<!DOCTYPE html>
<html lang="en">
<head>
<meta charset="utf-8">
<title>Pexla Business Card</title>
<link href="https://fonts.googleapis.com/css2?family=Roboto+Condensed:wght@700&family=Roboto:wght@400;700&display=swap" rel="stylesheet">
<style>
  :root {
    --backdrop: #3a3a3a;
    --backdrop-edge: #1c1c1c;
    --card-navy: #14134a;
    --card-navy-deep: #0d0c38;
    --ink-white: #f2f3fa;
    --ink-soft: #c9cbe2;
    --divider: #8a8cb5;
  }
  * { margin: 0; padding: 0; box-sizing: border-box; }
  html, body { width: 1200px; height: 900px; overflow: hidden; }
  body {
    background: radial-gradient(ellipse at center, var(--backdrop) 0%, var(--backdrop-edge) 100%);
    font-family: "Roboto", sans-serif;
    position: relative;
  }
  .card {
    position: absolute;
    left: 285px;
    width: 630px;
    height: 360px;
    background: linear-gradient(135deg, var(--card-navy) 0%, var(--card-navy-deep) 100%);
    border-radius: 4px;
    box-shadow: 0 14px 30px rgba(0,0,0,0.55);
    color: var(--ink-white);
  }
  .card--front { top: 60px; }
  .card--back { top: 480px; }

  .brand-name {
    position: absolute;
    left: 0; right: 0;
    top: 50%;
    transform: translateY(-50%);
    text-align: center;
    font-family: "Roboto", sans-serif;
    font-weight: 700;
    font-size: 110px;
    letter-spacing: -2px;
    color: var(--ink-white);
  }

  .identity {
    position: absolute;
    right: 340px;
    top: 120px;
    text-align: right;
  }
  .identity__name {
    font-family: "Roboto Condensed", sans-serif;
    font-weight: 700;
    font-size: 24px;
    letter-spacing: 0.5px;
    text-transform: uppercase;
  }
  .identity__role {
    font-size: 15px;
    color: var(--ink-soft);
    margin-top: 4px;
  }
  .divider {
    position: absolute;
    left: 305px;
    top: 118px;
    width: 1px;
    height: 66px;
    background: var(--divider);
  }
  .contact {
    position: absolute;
    left: 325px;
    top: 116px;
    list-style: none;
    font-size: 17px;
    line-height: 24px;
  }
  .contact__item { display: flex; align-items: center; gap: 10px; }
  .contact__icon { width: 12px; height: 12px; fill: none; stroke: var(--ink-white); stroke-width: 1.4; }
  .address {
    position: absolute;
    left: 0; right: 0;
    bottom: 60px;
    text-align: center;
    font-size: 17px;
    color: var(--ink-white);
  }
</style>
</head>
<body>
  <section class="card card--front" aria-label="Card front">
    <div class="brand-name">Pexla</div>
  </section>

  <section class="card card--back" aria-label="Card back">
    <div class="identity">
      <div class="identity__name">Daniel Reyes</div>
      <div class="identity__role">Director</div>
    </div>
    <div class="divider"></div>
    <ul class="contact">
      <li class="contact__item">
        <svg class="contact__icon" viewBox="0 0 12 12"><path d="M3 1 L5 3.5 L4 5 Q5.5 7 7 8 L8.5 7 L11 9 L9.5 11 Q4 10 1 2.5 Z"/></svg>
        +61 2 5550 0193
      </li>
      <li class="contact__item">
        <svg class="contact__icon" viewBox="0 0 12 12"><rect x="1" y="2.5" width="10" height="7"/><path d="M1 2.5 L6 6.5 L11 2.5"/></svg>
        info@pexla.com
      </li>
      <li class="contact__item">
        <svg class="contact__icon" viewBox="0 0 12 12"><circle cx="6" cy="6" r="5"/><path d="M1 6 H11 M6 1 Q3 6 6 11 Q9 6 6 1"/></svg>
        www.pexla.com
      </li>
    </ul>
    <div class="address">18 Harbour Lane Sydney, NSW 2000</div>
  </section>
</body>
</html>
```